Business card design for new eCommerce site focusing on integrity and strong businsess tactics

We need a business card that will stand out and be memorable. Something with color that matches our company logo colors. Think high end version of Pactivo. There are 2 logos provided. The parent company is called Amber Ledge Partners and we are presenting a new and very exciting eCommerce site called BrightHarborTrade.example.

Target Market(s)

Our target markets are in the Activities, Food and Beverage, Health and Beauty

Industry/Entity Type

Marketing

Contact Information for Business Card

We have 4 members that need cards...I will provide all info to the winner of the design contest
Business Address is
4870 West 63rd Avenue, Suite C207
Phoenix AZ 85731

Font styles to use
Serif
Sans Serif

Colors

Designer to choose colors to be used in the design.

Requirements
Must have
• The card must be memorable...should be unique in design but must exude integrity and be playful .
• I have provided several colors or our parent company...please feel free to use which ever
Nice to have
• I will leave this up to you. Feel free to use other images of your choosing that wraps around our client.....Activities, Dining, Health, Beauty
Should not have
• just dont be boring

```html
<!DOCTYPE html>
<html lang="en">
<head>
<meta charset="utf-8">
<title>Amber Ledge Partners – Business Card</title>
<link rel="stylesheet" href="https://fonts.googleapis.com/css2?family=Roboto:wght@400;500;700&display=swap">
<style>
  :root {
    --backdrop: #b9b9b9;
    --lime: #8dbd3b;
    --teal: #3a9a98;
    --deep-teal: #1e7a82;
    --navy: #14264d;
    --ink: #2b2b2b;
    --paper: #f3f3f1;
    --white: #ffffff;
  }
  * { box-sizing: border-box; margin: 0; padding: 0; }
  html, body {
    width: 1200px; height: 576px; overflow: hidden;
    background: var(--backdrop);
    font-family: "Roboto", Arial, sans-serif;
  }
  .canvas { position: relative; width: 1200px; height: 576px; }

  .card {
    position: absolute;
    border-radius: 14px;
    overflow: hidden;
  }

  /* Front */
  .card-front {
    left: 80px; top: 138px; width: 486px; height: 294px;
    background: linear-gradient(180deg, var(--lime) 0%, #6fae4a 40%, var(--deep-teal) 78%, #1d7780 100%);
  }
  .front-emblem {
    position: absolute; left: 183px; top: 57px;
    width: 122px; height: 122px; border-radius: 50%;
    border: 1.5px solid var(--white);
  }
  .front-emblem::after {
    content: ""; position: absolute; inset: 4px; border-radius: 50%;
    background: var(--white);
  }
  .front-wordmark {
    position: absolute; left: 0; right: 0; top: 186px;
    text-align: center; color: var(--white); font-weight: 500;
  }
  .front-wordmark .name-main { display: block; font-size: 31px; line-height: 36px; }
  .front-wordmark .name-sub { display: block; font-size: 13px; letter-spacing: 5px; line-height: 14px; }

  /* Back */
  .card-back {
    left: 602px; top: 138px; width: 480px; height: 290px;
    background: var(--paper);
  }
  .back-wordmark {
    position: absolute; left: 18px; top: 30px;
    color: var(--teal); font-weight: 700;
  }
  .back-wordmark .name-main { display: block; font-size: 30px; line-height: 34px; }
  .back-wordmark .name-sub { display: block; font-size: 13px; letter-spacing: 4.5px; line-height: 12px; padding-left: 44px; }

  .hero-graphic {
    position: absolute; left: 336px; top: 24px; width: 134px; height: 266px;
    border-radius: 67px 67px 0 0;
    background: linear-gradient(180deg, #b7d77f 0%, #7fbcb8 45%, #5d6f94 100%);
    opacity: 0.85;
  }

  .person { position: absolute; left: 18px; top: 114px; }
  .person-name { font-size: 20px; font-weight: 700; color: var(--teal); line-height: 26px; }
  .person-title { font-size: 12px; color: var(--ink); line-height: 16px; }

  .contact-list { position: absolute; left: 18px; top: 180px; list-style: none; }
  .contact-list li {
    display: flex; align-items: center; gap: 10px;
    font-size: 13px; color: var(--ink); line-height: 18px;
  }
  .contact-list svg { width: 12px; height: 12px; fill: var(--teal); flex: none; }

  .address {
    position: absolute; left: 18px; top: 240px;
    font-size: 13px; line-height: 16px; color: var(--ink); font-style: normal;
  }

  .partner-mark {
    position: absolute; left: 206px; top: 246px;
    display: flex; align-items: center; gap: 5px;
    font-size: 13px; font-weight: 500; color: var(--lime);
  }
  .partner-mark .dot { width: 12px; height: 12px; border-radius: 50%; background: var(--teal); }
</style>
</head>
<body>
<main class="canvas">

  <section class="card card-front" aria-label="Card front">
    <div class="front-emblem" aria-hidden="true"></div>
    <div class="front-wordmark">
      <span class="name-main">Amber Ledge</span>
      <span class="name-sub">partners</span>
    </div>
  </section>

  <section class="card card-back" aria-label="Card back">
    <div class="back-wordmark">
      <span class="name-main">Amber Ledge</span>
      <span class="name-sub">partners</span>
    </div>

    <div class="hero-graphic" role="img" aria-label="Large brand graphic area in lime, teal and navy"></div>

    <div class="person">
      <p class="person-name">Employee Name</p>
      <p class="person-title">Managing Director</p>
    </div>

    <ul class="contact-list">
      <li>
        <svg viewBox="0 0 12 12" aria-hidden="true"><path d="M1 3.5C1 2 3 1.5 6 1.5s5 .5 5 2v1H8.5V3.6H3.5v.9H1zM3 5.5h6l1.5 4.5h-9z"/></svg>
        1800-555-0147
      </li>
      <li>
        <svg viewBox="0 0 12 12" aria-hidden="true"><path d="M0.5 2.5h11v7h-11z"/><path d="M1.2 3.2 6 6.8l4.8-3.6" stroke="#f3f3f1" stroke-width="1" fill="none"/></svg>
        name@brightharbortrade.example
      </li>
      <li>
        <svg viewBox="0 0 12 12" aria-hidden="true"><circle cx="6" cy="6" r="5.5"/><path d="M6 .5v11M.5 6h11M6 .5C3.5 3 3.5 9 6 11.5M6 .5c2.5 2.5 2.5 8.5 0 11" stroke="#f3f3f1" stroke-width=".8" fill="none"/></svg>
        www.brightharbortrade.example
      </li>
    </ul>

    <address class="address">4870 West 63rd Avenue, Suite<br>C207, Phoenix AZ 85731</address>

    <div class="partner-mark">
      <span class="dot" aria-hidden="true"></span>
      <span>Verdantly.example</span>
    </div>
  </section>

</main>
</body>
</html>
```